business card

Business card for new business.
Red and black corporate colors.
Card can have an Indsutrial feel to it. Feel free to add Rust, Bolted steel, or graphics as you see fit. We provide highly specialized services to the below mentioned industries.
Keep information out of corners so that if I want I can choose rounded corners.
Information
- front. name - title - phone - email
- Rear
Refining - Rail - Infrastructure - Mining - Energy
Calgary - Edmonton - Fort McMurray - Revelstoke - Vancouver

```html
<!DOCTYPE html>
<html lang="en">
<head>
<meta charset="utf-8">
<title>Girderline Business Card</title>
<link rel="stylesheet" href="https://fonts.googleapis.com/css2?family=Lato:wght@400;700;900&family=Oswald:wght@500&display=swap">
<style>
  :root {
    --stage: #3a3a3a;
    --stage-edge: #262626;
    --card: #050505;
    --red: #e3191f;
    --grey: #8a8888;
    --white: #f4f4f4;
  }
  * { box-sizing: border-box; margin: 0; padding: 0; }
  html, body { width: 1200px; height: 1200px; overflow: hidden; }
  body {
    background: radial-gradient(circle at 50% 40%, var(--stage) 0%, var(--stage-edge) 100%);
    font-family: "Lato", sans-serif;
    display: flex;
    flex-direction: column;
    align-items: center;
    justify-content: center;
    gap: 60px;
  }
  .card {
    position: relative;
    width: 860px;
    height: 491px;
    background: var(--card);
    box-shadow: 0 18px 40px rgba(0,0,0,0.5);
  }
  .card__frame {
    position: absolute;
    inset: 18px;
    border: 4px solid var(--red);
  }

  /* Front: brand and service areas */
  .card--front {
    display: flex;
    flex-direction: column;
    align-items: center;
    justify-content: center;
  }
  .brand {
    display: flex;
    align-items: center;
    gap: 20px;
    margin-top: -40px;
  }
  .brand__mark {
    width: 34px;
    height: 34px;
    background: var(--red);
  }
  .brand__name {
    font-family: "Lato", sans-serif;
    font-weight: 900;
    font-size: 86px;
    letter-spacing: 2px;
    color: var(--grey);
  }
  .coverage {
    position: absolute;
    left: 0; right: 0;
    bottom: 54px;
    text-align: center;
    color: var(--white);
    font-size: 24px;
    line-height: 1.35;
    letter-spacing: 0.5px;
  }
  .coverage .dot {
    display: inline-block;
    width: 7px; height: 7px;
    border-radius: 50%;
    background: var(--red);
    margin: 0 9px 4px;
    vertical-align: middle;
  }

  /* Back: person and contacts */
  .card--back {
    display: flex;
    align-items: center;
    justify-content: center;
    gap: 56px;
  }
  .person {
    text-align: right;
    margin-top: 20px;
  }
  .person__name {
    font-family: "Oswald", sans-serif;
    font-weight: 500;
    font-size: 66px;
    line-height: 1;
    color: var(--red);
  }
  .person__title {
    font-size: 25px;
    color: var(--white);
    margin-top: 4px;
  }
  .divider {
    width: 3px;
    height: 140px;
    background: var(--red);
  }
  .contact {
    color: var(--white);
    font-size: 24px;
    line-height: 1.3;
  }
  .contact__address { margin-bottom: 14px; }
  .contact__row {
    display: flex;
    align-items: center;
    gap: 18px;
  }
  .contact__row svg { width: 22px; height: 22px; flex: none; }
</style>
</head>
<body>

<section class="card card--front">
  <div class="card__frame"></div>
  <div class="brand">
    <span class="brand__mark"></span>
    <span class="brand__name">GIRDERLINE</span>
  </div>
  <div class="coverage">
    <p>Fabrication<span class="dot"></span>Pipelines<span class="dot"></span>Bridges<span class="dot"></span>Quarrying<span class="dot"></span>Utilities</p>
    <p>Ridgeford<span class="dot"></span>Calder Falls<span class="dot"></span>Port Ashby<span class="dot"></span>Millbrook<span class="dot"></span>Stonehaven</p>
  </div>
</section>

<section class="card card--back">
  <div class="card__frame"></div>
  <div class="person">
    <p class="person__name">Daniel Archer</p>
    <p class="person__title">Manager</p>
  </div>
  <div class="divider"></div>
  <div class="contact">
    <p class="contact__address">418 Forge Street<br>Dallas, TX 75201</p>
    <p class="contact__row">
      <svg viewBox="0 0 24 24" aria-hidden="true"><path fill="#e3191f" d="M6.6 10.8a15.1 15.1 0 0 0 6.6 6.6l2.2-2.2c.3-.3.7-.4 1-.2 1.1.4 2.3.6 3.6.6.6 0 1 .4 1 1V20c0 .6-.4 1-1 1A17 17 0 0 1 3 4c0-.6.4-1 1-1h3.5c.6 0 1 .4 1 1 0 1.3.2 2.5.6 3.6.1.3 0 .7-.2 1z"/></svg>
      555 014 2290
    </p>
    <p class="contact__row">
      <svg viewBox="0 0 24 24" aria-hidden="true"><rect x="2" y="5" width="20" height="14" fill="#e3191f"/><path d="M2 5l10 8 10-8" fill="none" stroke="#050505" stroke-width="2"/></svg>
      hello@girderline.com
    </p>
    <p class="contact__row">
      <svg viewBox="0 0 24 24" aria-hidden="true"><g fill="none" stroke="#e3191f" stroke-width="2"><circle cx="12" cy="12" r="9.5"/><ellipse cx="12" cy="12" rx="4" ry="9.5"/><path d="M2.5 12h19M4 7h16M4 17h16"/></g></svg>
      www.girderline.com
    </p>
  </div>
</section>

</body>
</html>
```